Professional & attention grabbing.

A business card design, front and back. I already have a logo I will attach, but I am open to something new as well.
Things to include:
Name:
Title:
Phone:
Email:
Wanting something that is professional but attention grabbing.
Also we do a lot of work using drones on natural gas pipelines (leading the future)if you want to include any of that. I'm open to ideas.
Target Market(s)
Natural gas transmission industry / greenhouse gas mitigation industry
Industry/Entity Type
Business
Colors
Designer to choose colors to be used in the design.
Look and feel
Each slider illustrates characteristics of the customer's brand and the style your logo design should communicate.

```html
<!DOCTYPE html>
<html lang="en">
<head>
<meta charset="utf-8">
<title>Veyra Field Inspections – Business Card</title>
<link href="https://fonts.googleapis.com/css2?family=Poppins:wght@400;600&display=swap" rel="stylesheet">
<style>
  :root {
    --stage: #c2c2c2;
    --card: #111111;
    --card-edge: #1a1a1a;
    --brand-grey: #3b3b3d;
    --accent-red: #c8232b;
    --text-light: #f2f2f2;
    --map-tone: #242426;
  }
  * { margin: 0; padding: 0; box-sizing: border-box; }
  html, body {
    width: 1200px;
    height: 1000px;
    overflow: hidden;
    background: var(--stage);
    font-family: "Poppins", sans-serif;
  }
  .stage {
    position: relative;
    width: 1200px;
    height: 1000px;
  }
  .card {
    position: absolute;
    top: 345px;
    width: 540px;
    height: 310px;
    background: var(--card);
    border: 1px solid var(--card-edge);
    box-shadow: 0 6px 18px rgba(0,0,0,0.35);
    overflow: hidden;
  }
  .card--front { left: 45px; }
  .card--back { left: 615px; }

  .brand {
    position: absolute;
    display: flex;
    align-items: center;
    gap: 10px;
  }
  .brand__mark {
    width: 22px;
    height: 22px;
    background: var(--accent-red);
    flex: none;
  }
  .brand__name {
    font-weight: 600;
    color: var(--brand-grey);
    line-height: 1.05;
    text-transform: uppercase;
    letter-spacing: 0.02em;
  }
  .card--front .brand { left: 46px; top: 40px; }
  .card--front .brand__name { font-size: 19px; }

  .holder {
    position: absolute;
    left: 46px;
    bottom: 50px;
  }
  .holder__name {
    color: var(--accent-red);
    font-weight: 600;
    font-size: 18px;
    letter-spacing: 0.03em;
    text-transform: uppercase;
    line-height: 1.2;
  }
  .holder__title {
    color: var(--text-light);
    font-weight: 600;
    font-size: 13px;
    text-transform: uppercase;
    letter-spacing: 0.03em;
  }

  .contact {
    position: absolute;
    left: 350px;
    bottom: 48px;
    list-style: none;
  }
  .contact__item {
    display: flex;
    align-items: center;
    gap: 9px;
    color: var(--text-light);
    font-size: 12px;
    line-height: 1.65;
  }
  .contact__icon { width: 10px; height: 10px; flex: none; }

  .world-map {
    position: absolute;
    left: 30px;
    top: 20px;
    width: 480px;
    height: 265px;
    border-radius: 40px;
    background: radial-gradient(ellipse at center, var(--map-tone) 0%, rgba(36,36,38,0.6) 55%, rgba(17,17,17,0) 80%);
  }
  .card--back .brand {
    left: 50%;
    top: 50%;
    transform: translate(-50%, -50%);
  }
  .card--back .brand__mark { width: 30px; height: 30px; }
  .card--back .brand__name { font-size: 26px; }
</style>
</head>
<body>
<main class="stage">

  <section class="card card--front" aria-label="Card front">
    <div class="brand">
      <span class="brand__mark"></span>
      <span class="brand__name">Veyra Field<br>Inspections</span>
    </div>

    <div class="holder">
      <p class="holder__name">Dana Okafor</p>
      <p class="holder__title">Founder</p>
    </div>

    <ul class="contact">
      <li class="contact__item">
        <svg class="contact__icon" viewBox="0 0 10 10" aria-hidden="true">
          <path d="M1 3 Q5 0 9 3 L8 4.5 L6.5 3.8 L6.5 3 Q5 2.5 3.5 3 L3.5 3.8 L2 4.5 Z" fill="#c8232b"/>
          <rect x="2" y="5" width="6" height="4" rx="0.8" fill="#c8232b"/>
        </svg>
        <span>000 000 0000</span>
      </li>
      <li class="contact__item">
        <svg class="contact__icon" viewBox="0 0 10 10" aria-hidden="true">
          <rect x="0.5" y="2" width="9" height="6.5" rx="0.6" fill="#c8232b"/>
          <path d="M0.8 2.4 L5 5.8 L9.2 2.4" stroke="#111111" stroke-width="0.9" fill="none"/>
        </svg>
        <span>info@veyrafield.com</span>
      </li>
    </ul>
  </section>

  <section class="card card--back" aria-label="Card back">
    <div class="world-map" role="img" aria-label="Faint dotted world map spanning the card"></div>
    <div class="brand">
      <span class="brand__mark"></span>
      <span class="brand__name">Veyra Field<br>Inspections</span>
    </div>
  </section>

</main>
</body>
</html>
```